holloway paving service

Needs to have phone number 0418259730 and email markholloway@brightmail.com.au.
ABN 62318470915
name mark holloway

For all your concreting solutions
Excavation
Exposed & colour concrete
House & shed slabs
Driveways
Landing & steps

Contact Information for Business Card

ph 0418259730
email markholloway@brightmail.com.au.
ABN 62318470915
name mark holloway

```html
<!DOCTYPE html>
<html lang="en">
<head>
<meta charset="utf-8">
<title>Holloway Paving Service – Business Card</title>
<link rel="stylesheet" href="https://fonts.googleapis.com/css2?family=Roboto:wght@400;500;700&family=Roboto+Condensed:wght@400;700&display=swap">
<style>
  :root {
    --orange: #f26a21;
    --white: #ffffff;
    --paper: #fbfbfa;
    --ink: #4a4a4a;
    --grey: #8a8a8a;
    --backdrop: #e9e7e3;
  }
  * { box-sizing: border-box; margin: 0; padding: 0; }
  html, body {
    width: 1200px; height: 950px; overflow: hidden;
    background: var(--backdrop);
    font-family: "Roboto", Arial, sans-serif;
  }
  .canvas { position: relative; width: 1200px; height: 950px; }

  .card {
    position: absolute;
    width: 640px; height: 366px;
    box-shadow: 0 6px 18px rgba(0,0,0,0.18);
  }

  /* Front */
  .card--front { left: 90px; top: 80px; background: var(--paper); }
  .brand {
    position: absolute; left: 48px; top: 140px;
    display: flex; align-items: center; gap: 18px;
  }
  .brand__square { width: 44px; height: 44px; background: var(--orange); flex: none; }
  .brand__rule { width: 2px; height: 82px; background: var(--orange); flex: none; }
  .brand__text { display: flex; flex-direction: column; gap: 3px; }
  .brand__name {
    font-family: "Roboto Condensed", Arial, sans-serif;
    font-weight: 700; font-size: 19px; letter-spacing: 0.5px;
    color: var(--orange); white-space: nowrap;
  }
  .brand__sub {
    display: flex; align-items: center; gap: 8px;
    font-family: "Roboto Condensed", Arial, sans-serif;
    font-size: 15px; letter-spacing: 3px; color: var(--grey);
  }
  .brand__sub::before, .brand__sub::after {
    content: ""; height: 1px; width: 30px; background: var(--grey);
  }
  .brand__phone {
    font-family: "Roboto Condensed", Arial, sans-serif;
    font-size: 16px; letter-spacing: 2px; color: var(--orange);
  }

  .contact { position: absolute; left: 372px; top: 108px; width: 240px; }
  .contact__name {
    font-family: "Roboto Condensed", Arial, sans-serif;
    font-weight: 700; font-size: 24px; color: var(--orange);
    padding-bottom: 12px; border-bottom: 1.5px solid var(--orange);
    margin-bottom: 14px;
  }
  .contact__list { list-style: none; }
  .contact__item {
    display: flex; align-items: center; gap: 8px;
    font-size: 13px; color: var(--ink); line-height: 24px; white-space: nowrap;
  }
  .contact__item svg { width: 12px; height: 12px; fill: var(--orange); flex: none; }
  .contact__abn { margin-top: 2px; }

  /* Back */
  .card--back { left: 470px; top: 500px; background: var(--orange); overflow: hidden; }
  .services {
    position: absolute; left: 36px; top: 30px;
    color: var(--white); font-size: 15px; line-height: 22px;
  }
  .services__dot { font-size: 9px; vertical-align: 2px; margin: 0 6px; }
  .back-brand {
    position: absolute; left: 0; right: 0; top: 166px;
    display: flex; justify-content: center; align-items: center; gap: 12px;
  }
  .back-brand__dot { width: 14px; height: 14px; border-radius: 50%; background: var(--white); flex: none; }
  .back-brand__name {
    font-family: "Roboto Condensed", Arial, sans-serif;
    font-weight: 700; font-size: 26px; letter-spacing: 1px; color: var(--white);
  }
</style>
</head>
<body>
<main class="canvas">

  <section class="card card--front" aria-label="Business card front">
    <div class="brand">
      <div class="brand__square"></div>
      <div class="brand__rule"></div>
      <div class="brand__text">
        <span class="brand__name">HOLLOWAY PAVING</span>
        <span class="brand__sub">SERVICE</span>
        <span class="brand__phone">0418259730</span>
      </div>
    </div>

    <div class="contact">
      <h1 class="contact__name">MARK HOLLOWAY</h1>
      <ul class="contact__list">
        <li class="contact__item">
          <svg viewBox="0 0 24 24"><path d="M6.6 10.8a15.1 15.1 0 0 0 6.6 6.6l2.2-2.2a1 1 0 0 1 1-.25 11.4 11.4 0 0 0 3.6.57 1 1 0 0 1 1 1V20a1 1 0 0 1-1 1A17 17 0 0 1 3 4a1 1 0 0 1 1-1h3.5a1 1 0 0 1 1 1c0 1.25.2 2.45.57 3.57a1 1 0 0 1-.25 1z"/></svg>
          0418259730
        </li>
        <li class="contact__item">
          <svg viewBox="0 0 24 24"><path d="M2 5h20v14H2z M2 5l10 8 10-8"/></svg>
          markholloway@brightmail.com.au
        </li>
        <li class="contact__item">
          <svg viewBox="0 0 24 24"><circle cx="12" cy="12" r="11"/></svg>
          www.hollowaypaving.com.au
        </li>
        <li class="contact__item contact__abn">ABN 62318470915</li>
      </ul>
    </div>
  </section>

  <section class="card card--back" aria-label="Business card back">
    <p class="services">
      Excavation<span class="services__dot">◆</span>Exposed &amp; colour concrete<br>
      House &amp; shed slabs<span class="services__dot">◆</span>Driveways<span class="services__dot">◆</span>Landing &amp; steps
    </p>
    <div class="back-brand">
      <span class="back-brand__dot"></span>
      <span class="back-brand__name">HOLLOWAY PAVING SERVICE</span>
    </div>
  </section>

</main>
</body>
</html>
```